Need a Wordpress website for my HVAC company

I need a Wordpress website created for an HVAC company in a competitive market.
Following are some websites I like:
My current website is www.borvicoheating.com - we also have a facebook page with some pictures

We are an airconditioning and heating company that does both residential and commmercial work.
We need the following info on our website:
-mobile friendly
-Schedule an appt -repair/maintnenace/installation (i would like this option to always be on the page even if they scroll down.)
-24 hour service
-coupons /promotions
-financing
-reviews/testimonials
-about
-blog
-Our service area
The following are services we provide:
-Air conditioning - Installation/Service/Maintenance/new construction
-Heating - Installation/Service/Maintenance/new construction ( gas furnace, 2 stage furnace, electric heat)
-Duct - Repair/Replacement/Istallation - (zone systems)
-thermostats (wifi)
-Heat pump
-Air handler
-self communicating systems
-carbon monoxide testing
-hail damage
-duct sealing
-insulation
-Air cleaners - UV Air purifiers
-humidifiers

I would also like Quilbo SEO add on

Target Market(s)

Anyone who needs our services HVAC contractor

Industry/Entity Type

Hvac

Contact Information for Business Card

Phone:480-555-2046
website:www.borvicoheating.com
email pmarsh@borvicoheating.com

Coding

Coded - Design and coding required

Number of Pages Required

5+ page

Font styles to use
Serif
Sans Serif

Requirements
Must have
• I wrote in brief. I already have Webly Nest. Long story I paid for 3 years already. I need someone to put website there. Ive never used Wordpress but would like a template page so I can easily add services.
Nice to have
• Clean, bright, original

```html
<!DOCTYPE html>
<html lang="en">
<head>
<meta charset="utf-8">
<title>Borvico Heating – Heating &amp; Cooling</title>
<link href="https://fonts.googleapis.com/css2?family=Open+Sans:wght@400;600;700&display=swap" rel="stylesheet">
<style>
:root{
  --red:#c8202f;
  --blue:#16569f;
  --blue-dark:#0f4687;
  --ink:#2b2b2b;
  --text:#6d6d6d;
  --light:#f1f1f3;
  --footer:#efefef;
  --bar:#3a3a3a;
  --white:#fff;
}
*{box-sizing:border-box;margin:0;padding:0}
html,body{width:1200px;height:2799px;overflow:hidden}
body{font-family:"Open Sans",Arial,sans-serif;color:var(--text);background:var(--white);position:relative}
.section{position:relative;width:1200px}
.abs{position:absolute}

/* header */
.site-header{height:177px}
.brand{left:134px;top:52px;display:flex;align-items:center;gap:12px}
.brand-mark{width:34px;height:34px;background:var(--red);border-radius:50%}
.brand-name{font-size:30px;font-weight:700;color:var(--blue);letter-spacing:.5px;white-space:nowrap}
.header-contact{right:134px;top:50px;text-align:right;color:var(--ink)}
.header-contact .hours{font-size:12px}
.header-contact .slogan{font-size:14px}
.header-contact .call{font-size:24px;font-weight:700;color:var(--blue);display:flex;align-items:center;justify-content:flex-end;gap:8px;margin-top:2px}

/* nav */
.main-nav{height:38px;background:var(--red)}
.main-nav ul{list-style:none;display:flex;position:absolute;left:131px;top:0;height:38px}
.main-nav li{color:var(--white);font-size:12px;font-weight:600;padding:0 20px;line-height:38px;text-transform:uppercase}
.main-nav li.active{background:#a81825;display:flex;align-items:center;gap:6px}

/* hero */
.hero{height:397px;background:linear-gradient(90deg,#e9ebee 0%,#f5f6f8 45%,#eef0f3 100%);overflow:hidden}
.hero-unit{left:200px;top:0;width:434px;height:360px;background:linear-gradient(180deg,#fbfbfb,#dcdfe3)}
.hero-mascot{left:850px;top:34px;width:220px;height:363px;background:linear-gradient(180deg,#e4e8ee 0%,#c3d3e6 100%)}
.hero-copy{left:500px;top:78px;width:336px;text-align:right}
.hero-copy h1{font-size:24px;line-height:30px;color:var(--red);font-weight:700;text-transform:uppercase}
.hero-copy p{font-size:15px;color:var(--blue);font-weight:600}
.hero-arrow{top:186px}

/* schedule */
.schedule{height:362px;background:var(--blue)}
.schedule h2{position:absolute;top:38px;width:100%;text-align:center;color:var(--white);font-size:23px;font-weight:700}
.tabs{left:424px;top:74px;display:flex;background:var(--white);height:40px}
.tab{width:126px;font-size:14px;line-height:40px;text-align:center;color:var(--text)}
.tab.active{background:#2f2f2f;color:var(--white);position:relative}
.tab.active::after{content:"";position:absolute;left:55px;bottom:-8px;border:8px solid transparent;border-top-color:#2f2f2f;border-bottom:0}
.field{background:var(--white);height:42px;font-size:11px;color:#9a9a9a;padding:0 18px;line-height:42px}
.submit{left:561px;top:284px;width:78px;height:39px;background:#2b2b2b;color:var(--white);font-size:11px;line-height:39px;text-align:center;text-transform:uppercase}

/* headings */
.section-title{position:absolute;width:100%;text-align:center;color:var(--blue);font-size:23px;font-weight:700;text-transform:uppercase}

/* why choose */
.why{height:406px}
.feature{width:280px}
.feature h3{font-size:17px;font-weight:400;color:var(--red);margin:8px 0 4px}
.feature p{font-size:10px;line-height:14px;color:var(--text)}

/* about */
.about{height:370px}
.about-media{left:131px;top:42px;width:458px;height:264px;border:1px solid var(--red);padding:10px}
.about-photo{width:100%;height:100%;background:linear-gradient(135deg,#c9d6e2,#e9eef2 55%,#2e5d9c);position:relative}
.play{position:absolute;left:50%;top:50%;transform:translate(-50%,-50%)}
.about-copy{left:616px;top:38px;width:453px}
.about-copy h2{font-size:23px;color:var(--blue);font-weight:700;margin-bottom:12px}
.about-copy p{font-size:12.5px;line-height:21px;text-align:justify}
.btn{display:inline-block;color:var(--white);font-size:13px;text-align:center}
.btn-read{margin-top:26px;background:var(--blue);width:96px;height:40px;line-height:40px;font-size:11px}

/* services */
.services{height:519px;background:var(--light)}
.thermostat{left:130px;top:120px;width:340px;height:399px;background:linear-gradient(180deg,#fafafa 0%,#e3e4e6 55%,#e8d3c2 100%)}
.service-list{list-style:none}
.service-list li{font-size:16px;color:var(--red);height:44px;display:flex;align-items:center;gap:10px}
.btn-res{left:545px;top:433px;width:235px;height:43px;line-height:43px;background:var(--red);font-size:14px}
.btn-com{left:793px;top:433px;width:232px;height:43px;line-height:43px;background:var(--blue);font-size:14px}

/* testimonials */
.testimonials{height:299px}
.quote{left:131px;top:104px;width:938px;text-align:center}
.quote .lead{font-size:16px;color:var(--ink)}
.quote .body{font-size:11px;line-height:18px;margin-top:6px}
.qmark{font-size:30px;color:#bbb;font-family:Georgia,serif;vertical-align:-8px;line-height:0}
.reviewer{left:512px;top:207px;display:flex;align-items:center;gap:14px}
.avatar{width:56px;height:56px;border-radius:50%;background:#d4d7da;border:3px solid var(--white);box-shadow:0 0 0 1px #ddd}
.reviewer .name{font-size:15px;color:var(--red)}
.stars{display:flex;gap:3px;margin-top:4px}

/* footer */
.site-footer{height:159px;background:var(--footer)}
.site-footer h4{font-size:11px;color:var(--red);font-weight:700;text-transform:uppercase;margin-bottom:6px;line-height:15px}
.site-footer ul{list-style:none}
.site-footer li{font-size:10px;line-height:21px;color:var(--ink)}
.contact-list li{display:flex;align-items:center;gap:8px}
.cards{display:flex;gap:6px;margin-top:8px}
.card{width:36px;height:18px;background:#d7d9dc;border:1px solid #c5c5c5}
.footer-brand{left:134px;top:48px;display:flex;align-items:center;gap:8px}
.footer-brand .brand-mark{width:18px;height:18px}
.footer-brand .brand-name{font-size:15px;letter-spacing:0}

.copyright{height:71px;background:var(--bar)}
.copyright p{position:absolute;left:131px;top:27px;font-size:11px;color:var(--white)}
.social{right:131px;top:24px;display:flex;gap:8px}
.social span{width:24px;height:24px;border-radius:50%}
</style>
</head>
<body>

<header class="section site-header">
  <div class="abs brand"><span class="brand-mark"></span><span class="brand-name">Borvico Heating</span></div>
  <div class="abs header-contact">
    <div class="hours">24 hours a day ~ 7 days a week</div>
    <div class="slogan">Service with Integrity</div>
    <div class="call">
      <svg width="14" height="20" viewBox="0 0 14 20"><rect x="1" y="1" width="12" height="18" rx="2" fill="none" stroke="#16569f" stroke-width="2"/><circle cx="7" cy="15.5" r="1.3" fill="#16569f"/></svg>
      Call (480) 555-2046
    </div>
  </div>
</header>

<nav class="section main-nav">
  <ul>
    <li class="active"><svg width="12" height="11" viewBox="0 0 12 11"><path d="M6 0 0 5h2v6h3V7h2v4h3V5h2z" fill="#fff"/></svg>Home</li>
    <li>About Us</li><li>24 Hour Services</li><li>Coupons</li><li>Financing</li><li>Reviews</li><li>Blog</li><li>Contact Us</li>
  </ul>
</nav>

<section class="section hero">
  <div class="abs hero-unit" role="img" aria-label="Wall-mounted split air conditioner unit"></div>
  <div class="abs hero-mascot" role="img" aria-label="Illustrated service technician holding a thermometer"></div>
  <div class="abs hero-copy">
    <h1>Your satisfaction is guaranteed</h1>
    <p>Our Reputation Depends on it</p>
  </div>
  <svg class="abs hero-arrow" style="left:22px" width="16" height="26" viewBox="0 0 16 26"><path d="M14 2 3 13l11 11" fill="none" stroke="#8a8a8a" stroke-width="4"/></svg>
  <svg class="abs hero-arrow" style="right:22px" width="16" height="26" viewBox="0 0 16 26"><path d="M2 2l11 11L2 24" fill="none" stroke="#8a8a8a" stroke-width="4"/></svg>
</section>

<section class="section schedule">
  <h2>SCHEDULE AN APPOINTMENT</h2>
  <div class="abs tabs"><div class="tab active">Installation</div><div class="tab">Maintenance</div><div class="tab">Repair</div></div>
  <div class="abs field" style="left:131px;top:155px;width:220px">Name</div>
  <div class="abs field" style="left:370px;top:155px;width:220px">Email</div>
  <div class="abs field" style="left:609px;top:155px;width:220px">Phone</div>
  <div class="abs field" style="left:847px;top:155px;width:220px;display:flex;justify-content:space-between;align-items:center">Service for
    <svg width="10" height="6" viewBox="0 0 10 6"><path d="M1 1l4 4 4-4" fill="none" stroke="#777" stroke-width="1.5"/></svg></div>
  <div class="abs field" style="left:131px;top:218px;width:459px">Address</div>
  <div class="abs field" style="left:609px;top:218px;width:458px">Message</div>
  <div class="abs submit">Submit</div>
</section>

<section class="section why">
  <h2 class="section-title" style="top:70px">Why Choose Us</h2>
  <div class="abs feature" style="left:131px;top:128px">
    <svg width="22" height="22" viewBox="0 0 22 22"><circle cx="11" cy="11" r="9" fill="none" stroke="#c8202f" stroke-width="2.5"/><path d="M11 5v6h4" fill="none" stroke="#c8202f" stroke-width="2.5"/></svg>
    <h3>24/7 Emergency Service</h3>
    <p>You need air conditioning service when you need it, not when we feel like being open. Call now. No need to wait!</p>
  </div>
  <div class="abs feature" style="left:457px;top:128px">
    <svg width="22" height="22" viewBox="0 0 22 22"><rect x="2" y="4" width="18" height="16" fill="none" stroke="#c8202f" stroke-width="2.5"/><path d="M2 9h18M7 1v5M15 1v5" stroke="#c8202f" stroke-width="2.5"/></svg>
    <h3>Same Day Service</h3>
    <p>You deserve a fast solution to your problem. We provide it - right away.</p>
  </div>
  <div class="abs feature" style="left:784px;top:128px">
    <svg width="26" height="22" viewBox="0 0 26 22"><circle cx="13" cy="6" r="4.5" fill="#c8202f"/><circle cx="5" cy="8" r="3.5" fill="#c8202f"/><circle cx="21" cy="8" r="3.5" fill="#c8202f"/><path d="M5 21c0-6 3-9 8-9s8 3 8 9z" fill="#c8202f"/><path d="M0 20c0-5 2-7 5-7l1 7zM26 20c0-5-2-7-5-7l-1 7z" fill="#c8202f"/></svg>
    <h3>Highly Trained Technicians</h3>
    <p>will install or repair your brand air conditioning and heating system for top reliability, energy savings, and property value.</p>
  </div>
  <div class="abs feature" style="left:131px;top:256px">
    <svg width="16" height="22" viewBox="0 0 16 22"><path d="M9 0 1 13h6l-2 9 10-14H9z" fill="#c8202f"/></svg>
    <h3>Free Energy Survey</h3>
    <p>for replacement air conditioning and heating systems. Let us help you get maximum comfort and savings. No obligation.</p>
  </div>
  <div class="abs feature" style="left:457px;top:256px">
    <svg width="24" height="22" viewBox="0 0 24 22"><rect x="1" y="3" width="22" height="16" fill="none" stroke="#c8202f" stroke-width="2.5"/><circle cx="12" cy="11" r="4" fill="#c8202f"/></svg>
    <h3>Pay by the Job, Not by the Hour</h3>
    <p>our up-front, flat rate pricing lets you know exactly what to expect for your air conditioning service or replacement.</p>
  </div>
  <div class="abs feature" style="left:784px;top:256px">
    <svg width="22" height="22" viewBox="0 0 22 22"><rect x="1" y="9" width="5" height="12" fill="#c8202f"/><path d="M8 9l5-8c2 0 3 1 2 4l-1 3h6c1 0 2 1 1 3l-3 9c0 1-1 1-2 1H8z" fill="#c8202f"/></svg>
    <h3>Fairness and Honesty</h3>
    <p>Our technicians do not work on commission, which allows us to keep our prices down. That also means you can trust your technician to give you honest answers that are best for you and your families or businesses comfort.</p>
  </div>
</section>

<section class="section about">
  <div class="abs about-media">
    <div class="about-photo" role="img" aria-label="Technician servicing an indoor air conditioning unit">
      <svg class="play" width="46" height="46" viewBox="0 0 46 46"><circle cx="23" cy="23" r="22" fill="#c8202f"/><path d="M18 13l14 10-14 10z" fill="#fff"/></svg>
    </div>
  </div>
  <div class="abs about-copy">
    <h2>ABOUT US</h2>
    <p>Sed arcu justo, consectetur nec sapien et, pulvinar vestibulum nulla. Proin sodales, risus vitae fermentum faucibus, enim nunc elementum magna, in venenatis dui ligula ac justo. Quisque rhoncus tempor metus, eu porttitor nunc malesuada nec. Cras dolor ipsum, elementum non felis id, euismod egestas lorem. Vivamus id fringilla erat, a vestibulum arcu. Sed lobortis, dui eget tristique commodo, nulla dolor posuere turpis, ac fringilla sapien nulla et tortor. Sed auctor dolor neque, non bibendum velit sodales sit amet. Nulla gravida suscipit tortor, vel tristique lacus.</p>
    <span class="btn btn-read">Read more</span>
  </div>
</section>

<section class="section services">
  <h2 class="section-title" style="top:46px">Services We Provide Are</h2>
  <div class="abs thermostat" role="img" aria-label="Hand pressing a button on a digital wall thermostat"></div>
  <ul class="abs service-list" style="left:545px;top:107px">
    <li><svg width="14" height="14" viewBox="0 0 14 14"><circle cx="7" cy="7" r="6" fill="none" stroke="#c8202f" stroke-width="2"/><path d="M4 7l2 2 4-4" fill="none" stroke="#c8202f" stroke-width="2"/></svg>Air conditioning</li>
    <li><svg width="14" height="14" viewBox="0 0 14 14"><circle cx="7" cy="7" r="6" fill="none" stroke="#c8202f" stroke-width="2"/><path d="M4 7l2 2 4-4" fill="none" stroke="#c8202f" stroke-width="2"/></svg>Heating</li>
    <li><svg width="14" height="14" viewBox="0 0 14 14"><circle cx="7" cy="7" r="6" fill="none" stroke="#c8202f" stroke-width="2"/><path d="M4 7l2 2 4-4" fill="none" stroke="#c8202f" stroke-width="2"/></svg>Duct</li>
    <li><svg width="14" height="14" viewBox="0 0 14 14"><circle cx="7" cy="7" r="6" fill="none" stroke="#c8202f" stroke-width="2"/><path d="M4 7l2 2 4-4" fill="none" stroke="#c8202f" stroke-width="2"/></svg>Thermostats</li>
    <li><svg width="14" height="14" viewBox="0 0 14 14"><circle cx="7" cy="7" r="6" fill="none" stroke="#c8202f" stroke-width="2"/><path d="M4 7l2 2 4-4" fill="none" stroke="#c8202f" stroke-width="2"/></svg>Heat pump</li>
    <li><svg width="14" height="14" viewBox="0 0 14 14"><circle cx="7" cy="7" r="6" fill="none" stroke="#c8202f" stroke-width="2"/><path d="M4 7l2 2 4-4" fill="none" stroke="#c8202f" stroke-width="2"/></svg>Air handler</li>
    <li><svg width="14" height="14" viewBox="0 0 14 14"><circle cx="7" cy="7" r="6" fill="none" stroke="#c8202f" stroke-width="2"/><path d="M4 7l2 2 4-4" fill="none" stroke="#c8202f" stroke-width="2"/></svg>Self communicating systems</li>
  </ul>
  <ul class="abs service-list" style="left:840px;top:107px">
    <li><svg width="14" height="14" viewBox="0 0 14 14"><circle cx="7" cy="7" r="6" fill="none" stroke="#c8202f" stroke-width="2"/><path d="M4 7l2 2 4-4" fill="none" stroke="#c8202f" stroke-width="2"/></svg>carbon monoxide testing</li>
    <li><svg width="14" height="14" viewBox="0 0 14 14"><circle cx="7" cy="7" r="6" fill="none" stroke="#c8202f" stroke-width="2"/><path d="M4 7l2 2 4-4" fill="none" stroke="#c8202f" stroke-width="2"/></svg>Hail damage</li>
    <li><svg width="14" height="14" viewBox="0 0 14 14"><circle cx="7" cy="7" r="6" fill="none" stroke="#c8202f" stroke-width="2"/><path d="M4 7l2 2 4-4" fill="none" stroke="#c8202f" stroke-width="2"/></svg>Duct sealing</li>
    <li><svg width="14" height="14" viewBox="0 0 14 14"><circle cx="7" cy="7" r="6" fill="none" stroke="#c8202f" stroke-width="2"/><path d="M4 7l2 2 4-4" fill="none" stroke="#c8202f" stroke-width="2"/></svg>Insulation</li>
    <li><svg width="14" height="14" viewBox="0 0 14 14"><circle cx="7" cy="7" r="6" fill="none" stroke="#c8202f" stroke-width="2"/><path d="M4 7l2 2 4-4" fill="none" stroke="#c8202f" stroke-width="2"/></svg>Air cleaners</li>
    <li><svg width="14" height="14" viewBox="0 0 14 14"><circle cx="7" cy="7" r="6" fill="none" stroke="#c8202f" stroke-width="2"/><path d="M4 7l2 2 4-4" fill="none" stroke="#c8202f" stroke-width="2"/></svg>Humidifiers</li>
  </ul>
  <span class="abs btn btn-res">Book for Residential Service</span>
  <span class="abs btn btn-com">Book for Commercial Service</span>
</section>

<section class="section testimonials">
  <h2 class="section-title" style="top:56px">Testimonials</h2>
  <div class="abs quote">
    <div class="lead"><span class="qmark">&ldquo;</span> Pellentesque convallis molestie enim sit amet efficitur amet consequat risus.</div>
    <div class="body">Nullam accumsan purus vel tempus viverra. Mauris suscipit felis id nunc elementum varius. Praesent elementum nulla sit amet justo pellentesque scelerisque. Nam et tortor in ante iaculis porttitor in luctus mi. Vivamus gravida sem a pretium euismod. Nam lobortis, purus et. <span class="qmark">&rdquo;</span></div>
  </div>
  <div class="abs reviewer">
    <div class="avatar" role="img" aria-label="Customer portrait"></div>
    <div>
      <div class="name">Dale Hurst, City</div>
      <div class="stars">
        <svg width="14" height="14" viewBox="0 0 14 14"><path d="M7 0l2 5h5l-4 3 2 5-5-3-5 3 2-5-4-3h5z" fill="#f2b31b"/></svg>
        <svg width="14" height="14" viewBox="0 0 14 14"><path d="M7 0l2 5h5l-4 3 2 5-5-3-5 3 2-5-4-3h5z" fill="#f2b31b"/></svg>
        <svg width="14" height="14" viewBox="0 0 14 14"><path d="M7 0l2 5h5l-4 3 2 5-5-3-5 3 2-5-4-3h5z" fill="#f2b31b"/></svg>
        <svg width="14" height="14" viewBox="0 0 14 14"><path d="M7 0l2 5h5l-4 3 2 5-5-3-5 3 2-5-4-3h5z" fill="#f2b31b"/></svg>
        <svg width="14" height="14" viewBox="0 0 14 14"><path d="M7 0l2 5h5l-4 3 2 5-5-3-5 3 2-5-4-3h5z" fill="#f2b31b"/></svg>
      </div>
    </div>
  </div>
  <svg class="abs" style="left:22px;top:130px" width="12" height="22" viewBox="0 0 12 22"><path d="M10 2 2 11l8 9" fill="none" stroke="#999" stroke-width="2.5"/></svg>
  <svg class="abs" style="right:22px;top:130px" width="12" height="22" viewBox="0 0 12 22"><path d="M2 2l8 9-8 9" fill="none" stroke="#999" stroke-width="2.5"/></svg>
</section>

<footer class="section site-footer">
  <div class="abs footer-brand"><span class="brand-mark"></span><span class="brand-name">Borvico Heating</span></div>
  <div class="abs" style="left:308px;top:32px">
    <h4>Links</h4>
    <ul><li>• Home</li><li>• About us</li><li>• 24 hour services</li><li>• Coupons</li></ul>
  </div>
  <ul class="abs" style="left:444px;top:53px"><li>• Financing</li><li>• Reviews</li><li>• Blog</li><li>• Contact us</li></ul>
  <div class="abs" style="left:582px;top:32px">
    <h4>Contact Info</h4>
    <ul class="contact-list">
      <li><svg width="8" height="11" viewBox="0 0 8 11"><path d="M4 0a4 4 0 0 0-4 4c0 3 4 7 4 7s4-4 4-7a4 4 0 0 0-4-4z" fill="#444"/></svg>24 Building name, Street name, City - Zipcode</li>
      <li><svg width="8" height="11" viewBox="0 0 8 11"><rect x="1" y="0" width="6" height="11" rx="1" fill="#444"/></svg>Phone : (480) 555-2046</li>
      <li><svg width="10" height="8" viewBox="0 0 10 8"><rect width="10" height="8" fill="#444"/><path d="M0 0l5 4 5-4" fill="none" stroke="#efefef"/></svg>Email : info@borvicoheating.com</li>
    </ul>
  </div>
  <div class="abs" style="left:881px;top:32px">
    <h4 style="color:var(--ink)">We accept all credit cards</h4>
    <div class="cards"><span class="card"></span><span class="card"></span><span class="card"></span><span class="card"></span></div>
  </div>
</footer>

<div class="section copyright">
  <p>Copyright &copy; 2016 Company name. All rights reserved.</p>
  <div class="abs social">
    <span style="background:#3b5b9a"></span><span style="background:#2aa3d8"></span><span style="background:#1d77b4"></span><span style="background:#d6432f"></span>
  </div>
</div>

</body>
</html>
```